Tech business card design

We need an amazing business card design for our new business 'Pexla' a marketing tech startup based in Sydney, Australia. We provide an online marketplace for businesses to search and buy advertising media, connect with service providers and learn more about marketing. We wish to communicate 'cool tech', reliability and professionalism and design based around our logo.

Target Market(s)

Business Owners

Contact Information for Business Card

Name
Position
Email Address
Website
Phone Number

Font styles to use
Other font styles liked:
• Avenir & Avenir Next

Colors

Designer to choose colors to be used in the design.

```html
<!DOCTYPE html>
<html lang="en">
<head>
<meta charset="utf-8">
<title>Pexla business card</title>
<link href="https://fonts.googleapis.com/css2?family=Nunito+Sans:wght@400;700;900&display=swap" rel="stylesheet">
<style>
  :root {
    --backdrop: #e0dcdd;
    --card-front: #ffffff;
    --card-back: #848799;
    --ink: #14143a;
    --ink-soft: #25284a;
    --edge: #3a3a3a;
  }
  * { margin: 0; padding: 0; box-sizing: border-box; }
  html, body {
    width: 975px; height: 1200px; overflow: hidden;
    background: var(--backdrop);
    font-family: "Nunito Sans", sans-serif;
    color: var(--ink-soft);
  }
  .canvas { position: relative; width: 975px; height: 1200px; }
  .card {
    position: absolute; left: 56px; width: 864px; height: 495px;
    border-radius: 33px;
  }
  .card--front { top: 79px; background: var(--card-front); border: 1px solid var(--edge); }
  .card--back { top: 639px; background: var(--card-back); }

  .wordmark {
    position: absolute;
    font-weight: 900; color: var(--ink);
    line-height: 1; letter-spacing: -2px;
  }
  .card--front .wordmark { left: 74px; top: 22px; font-size: 158px; }
  .card--back .wordmark {
    left: 0; right: 0; top: 160px; text-align: center; font-size: 158px;
  }

  .holder { position: absolute; left: 77px; top: 206px; }
  .holder__name { font-size: 30px; font-weight: 700; color: var(--ink-soft); letter-spacing: 0.3px; line-height: 1.2; }
  .holder__role { font-size: 26px; font-weight: 400; line-height: 1.3; }

  .contacts { position: absolute; left: 77px; top: 311px; list-style: none; }
  .contacts li {
    display: flex; align-items: center; gap: 9px;
    font-size: 21px; height: 33px;
  }
  .contacts svg { width: 22px; height: 22px; flex: none; }

  .address {
    position: absolute; left: 540px; top: 330px;
    font-size: 21px; line-height: 29px; font-style: normal;
  }

  .back-url {
    position: absolute; left: 0; right: 0; top: 381px; text-align: center;
    font-size: 28px; letter-spacing: 4px; color: var(--ink-soft);
  }
</style>
</head>
<body>
<main class="canvas">
  <section class="card card--front">
    <div class="wordmark">pexla</div>
    <div class="holder">
      <p class="holder__name">MARA ELLISON</p>
      <p class="holder__role">Position</p>
    </div>
    <ul class="contacts">
      <li>
        <svg viewBox="0 0 24 24" aria-hidden="true">
          <circle cx="12" cy="12" r="10.5" fill="none" stroke="#14143a" stroke-width="2"/>
          <path d="M8.2 6.5l2 2.6-1.2 1.4c.8 1.7 2 2.9 3.6 3.7l1.4-1.2 2.6 2-1.3 2c-4.3-.4-8.4-4.5-8.8-8.8z" fill="#14143a"/>
        </svg>
        012-345-6789
      </li>
      <li>
        <svg viewBox="0 0 24 24" aria-hidden="true">
          <rect x="2" y="5" width="20" height="14" fill="#14143a"/>
          <path d="M2.5 5.5L12 13l9.5-7.5M2.5 18.5l7-6.5M21.5 18.5l-7-6.5" fill="none" stroke="#fff" stroke-width="1.6"/>
        </svg>
        info@pexla.com
      </li>
      <li>
        <svg viewBox="0 0 24 24" aria-hidden="true">
          <g fill="none" stroke="#14143a" stroke-width="1.6">
            <circle cx="12" cy="12" r="10"/>
            <ellipse cx="12" cy="12" rx="4.5" ry="10"/>
            <path d="M2 12h20M4 7h16M4 17h16"/>
          </g>
        </svg>
        www.pexla.com
      </li>
    </ul>
    <address class="address">Street name City Name,<br>Zipcode,012345</address>
  </section>

  <section class="card card--back">
    <div class="wordmark">pexla</div>
    <p class="back-url">www.pexla.com</p>
  </section>
</main>
</body>
</html>
```